its a new company based in Christchurch new Zealand building computers ,repairs, upgrades and anything computers for the general public,i like bright happy colours like yellows, greens reds anything that stands out and it needs to communicant trust and security towards my new company,i have no logo yet,

Target Market(s)

target market of all ages

Industry/Entity Type

Building

Contact Information for Business Card

Byte Harbour Limited,ph-0218847261,email-tidelark77@mailvesta.test,14c marlowe cres,fenwick

```html
<!DOCTYPE html>
<html lang="en">
<head>
<meta charset="utf-8">
<title>Byte Harbour Limited — Business Card</title>
<link rel="stylesheet" href="https://fonts.googleapis.com/css2?family=Orbitron:wght@500&family=Didact+Gothic&display=swap">
<style>
  :root {
    --ink: #333333;
    --yellow-pale: #fff8c8;
    --yellow-soft: #fdeb7a;
    --yellow-mid: #fcd94a;
    --yellow-deep: #fbc40a;
    --glow: #fffdf0;
  }
  html, body {
    margin: 0;
    padding: 0;
    overflow: hidden;
    background: #ffffff;
  }
  .card {
    position: relative;
    width: 1200px;
    height: 755px;
    overflow: hidden;
    color: var(--ink);
  }
  .card-background {
    position: absolute;
    inset: 0;
    width: 1200px;
    height: 755px;
  }
  .brand-mark {
    position: absolute;
    left: 52px;
    top: 42px;
    width: 150px;
    height: 150px;
    background: var(--ink);
  }
  .brand-name {
    position: absolute;
    left: 291px;
    top: 108px;
    margin: 0;
    font-family: "Orbitron", sans-serif;
    font-weight: 500;
    font-size: 43px;
    letter-spacing: 0.5px;
    line-height: 1;
    text-transform: uppercase;
    color: var(--ink);
    white-space: nowrap;
  }
  .services {
    position: absolute;
    left: 683px;
    top: 256px;
    margin: 0;
    padding: 0;
    list-style: none;
    font-family: "Didact Gothic", sans-serif;
    font-size: 37px;
    line-height: 49px;
  }
  .service {
    display: flex;
    align-items: center;
    gap: 16px;
    white-space: nowrap;
  }
  .service-icon {
    width: 30px;
    height: 30px;
    flex: none;
    margin-top: 8px;
  }
  .contact {
    position: absolute;
    left: 48px;
    top: 514px;
    margin: 0;
    padding: 0;
    list-style: none;
    font-family: "Didact Gothic", sans-serif;
    font-size: 41px;
    line-height: 61px;
  }
  .contact-item {
    display: flex;
    align-items: center;
    gap: 14px;
    white-space: nowrap;
  }
  .contact-icon {
    width: 44px;
    height: 44px;
    flex: none;
  }
</style>
</head>
<body>
<main class="card">
  <svg class="card-background" viewBox="0 0 1200 755" aria-hidden="true">
    <defs>
      <linearGradient id="base-fill" x1="0" y1="0" x2="1" y2="1">
        <stop offset="0" stop-color="var(--yellow-soft)"/>
        <stop offset="0.35" stop-color="var(--yellow-pale)"/>
        <stop offset="0.7" stop-color="var(--yellow-mid)"/>
        <stop offset="1" stop-color="var(--yellow-soft)"/>
      </linearGradient>
      <radialGradient id="sun-fill" cx="0.55" cy="0.35" r="0.7">
        <stop offset="0" stop-color="var(--yellow-soft)"/>
        <stop offset="0.6" stop-color="var(--yellow-mid)"/>
        <stop offset="1" stop-color="var(--yellow-deep)"/>
      </radialGradient>
      <radialGradient id="glow-fill" cx="0.5" cy="0.5" r="0.5">
        <stop offset="0" stop-color="var(--glow)" stop-opacity="1"/>
        <stop offset="1" stop-color="var(--glow)" stop-opacity="0"/>
      </radialGradient>
    </defs>
    <rect class="base" width="1200" height="755" fill="url(#base-fill)"/>
    <ellipse class="glow" cx="520" cy="150" rx="420" ry="330" fill="url(#glow-fill)"/>
    <circle class="sun" cx="1210" cy="150" r="520" fill="url(#sun-fill)"/>
    <path class="wave wave-upper" d="M0 300 C 220 200, 430 260, 620 400 S 1000 640, 1200 560 L1200 755 L0 755 Z" fill="var(--yellow-mid)" opacity="0.45"/>
    <path class="wave wave-lower" d="M0 470 C 250 360, 480 420, 700 560 S 1050 720, 1200 640 L1200 755 L0 755 Z" fill="var(--yellow-soft)" opacity="0.55"/>
    <path class="wave-line" d="M690 150 C 850 140, 1040 150, 1200 200" fill="none" stroke="var(--glow)" stroke-opacity="0.5" stroke-width="3"/>
  </svg>

  <div class="brand-mark" aria-hidden="true"></div>
  <h1 class="brand-name">Byte Harbour Limited</h1>

  <ul class="services">
    <li class="service">
      <svg class="service-icon" viewBox="0 0 30 30" aria-hidden="true"><path d="M15 3 V14" stroke="var(--ink)" stroke-width="4" stroke-linecap="round"/><path d="M8.5 7.5 A10 10 0 1 0 21.5 7.5" fill="none" stroke="var(--ink)" stroke-width="4" stroke-linecap="round"/></svg>
      <span>Building Computers</span>
    </li>
    <li class="service">
      <svg class="service-icon" viewBox="0 0 30 30" aria-hidden="true"><path d="M15 3 V14" stroke="var(--ink)" stroke-width="4" stroke-linecap="round"/><path d="M8.5 7.5 A10 10 0 1 0 21.5 7.5" fill="none" stroke="var(--ink)" stroke-width="4" stroke-linecap="round"/></svg>
      <span>Computer Repairs</span>
    </li>
    <li class="service">
      <svg class="service-icon" viewBox="0 0 30 30" aria-hidden="true"><path d="M15 3 V14" stroke="var(--ink)" stroke-width="4" stroke-linecap="round"/><path d="M8.5 7.5 A10 10 0 1 0 21.5 7.5" fill="none" stroke="var(--ink)" stroke-width="4" stroke-linecap="round"/></svg>
      <span>Computer Upgrades</span>
    </li>
  </ul>

  <ul class="contact">
    <li class="contact-item">
      <svg class="contact-icon" viewBox="0 0 44 44" aria-hidden="true"><circle cx="22" cy="22" r="18" fill="none" stroke="var(--ink)" stroke-width="2.5"/><path d="M17 12 c-3 1 -4 4 -3 9 c1 5 4 9 8 11 c2 1 4 0 5 -2 l-3 -4 l-3 1 c-2 -2 -3 -5 -3 -7 l3 -1 z" fill="none" stroke="var(--ink)" stroke-width="2.2" stroke-linejoin="round"/></svg>
      <span>021 884 7261</span>
    </li>
    <li class="contact-item">
      <svg class="contact-icon" viewBox="0 0 44 44" aria-hidden="true"><rect x="5" y="12" width="34" height="22" fill="none" stroke="var(--ink)" stroke-width="2.5"/><path d="M5 12 L22 25 L39 12 M5 34 L17 21 M39 34 L27 21" fill="none" stroke="var(--ink)" stroke-width="2.2"/></svg>
      <span>tidelark77@mailvesta.test</span>
    </li>
    <li class="contact-item">
      <svg class="contact-icon" viewBox="0 0 44 44" aria-hidden="true"><path d="M3 22 L22 5 L41 22 M9 17 V39 H19 V28 H25 V39 H35 V17" fill="none" stroke="var(--ink)" stroke-width="3" stroke-linejoin="round"/></svg>
      <span>14c marlowe Cres,Fenwick</span>
    </li>
  </ul>
</main>
</body>
</html>
```